Zielgruppe
Wir sind ein Netzwerk aus unabhängigen Tierarztpraxen und-kliniken.
Aufgabenstellung
1. Allgemeine Anforderungen:
Wir benötigen ein Set an Masterfolien für unsere Präsentationen. Als Orientierung stellen wir Ihnen einige Beispielfolien im Anhang zur Verfügung, die eine grobe Vorstellung davon vermitteln, wie das Design aussehen soll. Zudem empfehlen wir, sich auf unserer Homepage umzusehen, um sicherzustellen, dass das Design mit unserem bestehenden Corporate Design harmoniert.
2. Farbkonzept:
Bitte verwenden Sie unsere definierten Unternehmensfarben:
Gelb: #f7cd4e
Blau: #143357
Gold: #9d8030
Weiß: #ffffff
3. Schriftarten:
Unsere Unternehmensschriftarten sind:
Raleway
Century Gothic
Bitte stellen Sie sicher, dass diese Fonts durchgehend verwendet werden.
4. Farbvarianten:
Wir wünschen uns drei unterschiedliche Farbvarianten der Masterfolien:
Blaue Version: mit Blau als dominierende Farbe
Gelbe Version: mit Gelb als dominierende Farbe
Neutrale Version: weiß dominierend mit - eine ausgewogene Mischung mit gedeckteren Farben
5. Design-Elemente:
Das Design sollte modern, professionell und klar strukturiert sein.
Die Masterfolien sollen verschiedene Layouts enthalten (Titelfolie, Inhaltsfolie, Bild-Text-Kombinationen, etc.).
Bitte achten Sie darauf, dass genügend weißer Raum für eine aufgeräumte und übersichtliche Gestaltung bleibt.
Elemente wie Linien, Icons oder dezente Muster können genutzt werden, sollten jedoch nicht zu dominant wirken.
6. Format:
Die Masterfolien sollten für Microsoft PowerPoint optimiert sein und in 16:9 Format erstellt werden.

```html
<!DOCTYPE html>
<html lang="de">
<head>
<meta charset="utf-8">
<title>KLUVOTREN – Masterfolien</title>
<link href="https://fonts.googleapis.com/css2?family=Raleway:ital,wght@0,300;0,400;0,500;0,600;0,700;0,800;1,400;1,600&display=swap" rel="stylesheet">
<style>
:root{
  --yellow:#f7cd4e;
  --blue:#143357;
  --gold:#9d8030;
  --white:#ffffff;
  --page:#f1f1f1;
  --text:#143357;
  --rule:#f0d98c;
}
*{box-sizing:border-box;margin:0;padding:0}
html,body{width:1200px;height:2654px;overflow:hidden}
body{background:var(--page);font-family:'Raleway',sans-serif;color:var(--text);position:relative}
.slide{position:absolute;width:520px;height:293px;background:var(--white);overflow:hidden}
.slide.dark{background:var(--blue);color:var(--white)}
.abs{position:absolute}
.brand-mini{position:absolute;right:22px;top:20px;font-size:7px;font-weight:800;color:var(--gold);letter-spacing:.3px;display:flex;align-items:center;gap:3px}
.brand-mini i{display:block;width:8px;height:8px;background:var(--gold);border-radius:50%}
.s-title{position:absolute;left:40px;top:32px;font-size:20px;font-weight:800;color:var(--blue);line-height:1.1}
.s-title::before{content:"";position:absolute;left:0;top:-9px;width:24px;height:2px;background:var(--yellow)}
.foot{position:absolute;left:20px;bottom:14px;font-size:5.5px;color:var(--blue)}
.pg{position:absolute;right:0;bottom:0;width:72px;height:30px;background:var(--yellow);border-radius:10px 0 0 0;color:var(--white);font-size:20px;font-weight:700;text-align:center;line-height:31px}
.txt{font-size:6.6px;line-height:1.62;color:var(--text)}
.txt b{font-weight:800}
.lead{font-size:7px;font-weight:800;line-height:1.55}
.photo{position:absolute;border-radius:10px}
.ph-blue{background:linear-gradient(160deg,#3c5a7e,#1d3b62)}
.ph-light{background:linear-gradient(160deg,#e9ecef,#c9d0d8)}
.ph-warm{background:linear-gradient(160deg,#d7c9b8,#8f7d6a)}
.ph-green{background:linear-gradient(150deg,#cfd5d2,#3b8a4a)}
.btn{position:absolute;height:22px;background:var(--yellow);border-radius:11px;display:flex;align-items:center;gap:9px;padding-left:15px;font-size:8.5px;font-weight:700;color:var(--blue)}
.btn svg{width:10px;height:10px}
ul.dots{list-style:none}
ul.dots li::before{content:"• "}
.num-lite{font-size:17px;font-weight:300;color:var(--yellow)}
.icon-svg{stroke:var(--blue);fill:none;stroke-width:1.6;stroke-linecap:round;stroke-linejoin:round}
</style>
</head>
<body>

<!-- Titelfolie -->
<section class="slide dark" style="left:79px;top:105px">
  <div class="abs" style="left:38px;top:38px;display:flex;align-items:center;gap:8px;font-size:20px;font-weight:600;color:var(--yellow)"><span style="width:22px;height:22px;border-radius:50%;background:var(--yellow);display:block"></span>KLUVOTREN</div>
  <h1 class="abs" style="left:35px;top:114px;font-size:24px;font-weight:800;line-height:1.25">Your Presentation<br>Title <span style="color:var(--yellow)">Goes Here</span></h1>
  <div class="btn" style="left:35px;top:188px;width:182px"><svg viewBox="0 0 10 10"><path d="M1 0 L10 5 L1 10Z" fill="#143357"/></svg>Lorem ipsum dolor sit amet</div>
  <div class="abs" style="left:35px;bottom:14px;font-size:5.5px">07 Februar 2025 | Created by Lena Hausmann</div>
  <div class="abs" style="left:380px;bottom:14px;font-size:5.5px">info@kluvotren.de | www.kluvotren.de</div>
  <div class="photo ph-blue" style="left:277px;top:-10px;width:108px;height:90px" role="img" aria-label="Tierärztin bei der Behandlung eines Tieres"></div>
  <div class="photo ph-green" style="left:277px;top:91px;width:108px;height:143px" role="img" aria-label="Tierpflegerin mit Hund in der Praxis"></div>
  <div class="photo ph-blue" style="left:277px;top:245px;width:108px;height:60px;opacity:.7" role="img" aria-label="Praxisteam im Gespräch"></div>
  <div class="photo ph-light" style="left:393px;top:-10px;width:108px;height:59px;opacity:.6" role="img" aria-label="Praxisräume"></div>
  <div class="photo ph-light" style="left:393px;top:58px;width:108px;height:144px" role="img" aria-label="Team legt Hände zusammen"></div>
  <div class="photo ph-warm" style="left:393px;top:211px;width:108px;height:95px;opacity:.85" role="img" aria-label="Golden Retriever Welpe"></div>
</section>

<!-- Agenda 1 -->
<section class="slide" style="left:616px;top:105px">
  <h2 class="s-title" style="left:24px;top:30px">Today’s Agenda</h2>
  <div class="brand-mini"><i></i>KLUVOTREN</div>
  <div class="abs" style="left:0;top:150px;width:135px;height:143px;background:radial-gradient(circle at 100% 100%,transparent 45px,rgba(20,51,87,.22) 46px,rgba(20,51,87,.05) 130px,transparent 135px)" role="img" aria-label="Dezentes Punktmuster"></div>
  <div class="abs txt" style="left:98px;top:114px"><span style="color:var(--gold)">01</span></div>
  <div class="abs txt" style="left:124px;top:114px"><b>Lorem ipsum dolor sit amet</b><br>• Lorem ipsum dolor sit amet<br>• Lorem ipsum dolor sit amet</div>
  <div class="abs txt" style="left:268px;top:114px"><span style="color:var(--gold)">02</span></div>
  <div class="abs txt" style="left:294px;top:114px"><b>Lorem ipsum dolor sit amet</b><br>• Lorem ipsum dolor sit amet<br>• Lorem ipsum dolor sit amet</div>
  <div class="abs txt" style="left:143px;top:162px"><span style="color:var(--gold)">03</span></div>
  <div class="abs txt" style="left:169px;top:162px"><b>Lorem ipsum dolor sit amet</b><br>• Lorem ipsum dolor sit amet<br>• Lorem ipsum dolor sit amet</div>
  <div class="abs txt" style="left:313px;top:162px"><span style="color:var(--gold)">04</span></div>
  <div class="abs txt" style="left:339px;top:162px"><b>Lorem ipsum dolor sit amet</b><br>• Lorem ipsum dolor sit amet<br>• Lorem ipsum dolor sit amet</div>
  <div class="abs txt" style="left:171px;top:210px"><span style="color:var(--gold)">05</span></div>
  <div class="abs txt" style="left:197px;top:210px"><b>Lorem ipsum dolor sit amet</b><br>• Lorem ipsum dolor sit amet<br>• Lorem ipsum dolor sit amet</div>
  <div class="abs txt" style="left:341px;top:210px"><span style="color:var(--gold)">06</span></div>
  <div class="abs txt" style="left:367px;top:210px"><b>Lorem ipsum dolor sit amet</b><br>• Lorem ipsum dolor sit amet<br>• Lorem ipsum dolor sit amet</div>
</section>

<!-- Agenda 2 -->
<section class="slide" style="left:79px;top:416px">
  <h2 class="s-title" style="top:32px">Today’s Agenda</h2>
  <div class="brand-mini"><i></i>KLUVOTREN</div>
  <div class="abs" style="left:0;top:178px;width:230px;height:115px;background:var(--blue);border-radius:0 22px 0 0"></div>
  <div class="photo ph-light" style="left:41px;top:83px;width:163px;height:172px;border-radius:18px" role="img" aria-label="Tierärztin im Gespräch am Laptop"></div>
  <div class="abs txt" style="left:265px;top:90px;width:195px">
    <div style="display:flex;gap:18px;padding-bottom:9px;border-bottom:1px solid var(--rule)"><b>01</b><span>Lorem ipsum dolor sit amet, consectetuer adipiscing elit, sed diam nonummy.</span></div>
    <div style="display:flex;gap:18px;padding:9px 0;border-bottom:1px solid var(--rule);margin-top:5px"><b>02</b><span>Lorem ipsum dolor sit amet, consectetuer adipiscing elit, sed diam nonummy.</span></div>
    <div style="display:flex;gap:18px;padding:9px 0;border-bottom:1px solid var(--rule);margin-top:5px"><b>03</b><span>Lorem ipsum dolor sit amet, consectetuer adipiscing elit, sed diam nonummy.</span></div>
    <div style="display:flex;gap:18px;padding:9px 0;margin-top:5px"><b>04</b><span>Lorem ipsum dolor sit amet, consectetuer adipiscing elit, sed diam nonummy.</span></div>
  </div>
</section>

<!-- One Long Column -->
<section class="slide" style="left:616px;top:416px">
  <h2 class="s-title" style="top:36px;font-size:18px">One Long Column</h2>
  <div class="brand-mini"><i></i>KLUVOTREN</div>
  <div class="abs txt" style="left:40px;top:93px;width:448px">
    <p class="lead" style="width:230px">Lorem ipsum dolor sit amet, consectetuer adipiscing elit, sed diam nonummy nibh euismod tincidunt.</p>
    <p style="margin-top:14px">Lorem ipsum dolor sit amet, consectetuer adipiscing elit, sed diam nonummy nibh euismod tincidunt ut laoreet dolore magna aliquam erat volutpat. Ut wisi enim ad minim veniam, quis nostrud exerci tation ullamcorper suscipit lobortis nisl ut aliquip ex ea commodo consequat. Duis autem vel eum iriure dolor in hendrerit in vulputate velit esse molestie consequat, vel illum dolore eu feugiat nulla</p>
    <p style="margin-top:12px">Lorem ipsum dolor sit amet, consectetuer adipiscing elit, sed diam nonummy nibh euismod tincidunt ut laoreet dolore magna aliquam erat volutpat. Ut wisi enim ad minim veniam, quis nostrud exerci tation ullamcorper suscipit lobortis nisl ut aliquip ex ea commodo consequat. Duis autem vel eum iriure dolor in hendrerit in vulputate velit esse molestie consequat, vel illum dolore eu feugiat nulla</p>
  </div>
  <div class="foot">Your presentation Title Goes Here | www.kluvotren.de</div>
  <div class="pg">02</div>
</section>

<!-- Four Panel Point -->
<section class="slide" style="left:79px;top:727px">
  <h2 class="s-title">Four Panel Point</h2>
  <div class="brand-mini"><i></i>KLUVOTREN</div>
  <p class="abs txt" style="left:40px;top:74px;width:450px">Lorem ipsum dolor sit amet, consectetuer adipiscing elit, sed diam nonummy nibh euismod tincidunt ut laoreet dolore magna aliquam erat volutpat. Ut wisi enim ad minim veniam.</p>
  <div class="abs" style="left:38px;top:124px;width:102px;height:116px;background:var(--yellow);border-radius:4px"></div>
  <div class="abs" style="left:154px;top:124px;width:102px;height:116px;background:var(--yellow);border-radius:4px"></div>
  <div class="abs" style="left:271px;top:124px;width:102px;height:116px;background:var(--yellow);border-radius:4px"></div>
  <div class="abs" style="left:387px;top:124px;width:102px;height:116px;background:var(--yellow);border-radius:4px"></div>
  <svg class="abs" style="left:32px;top:117px" width="466" height="36" viewBox="0 0 466 36">
    <g><rect x="0" y="0" width="34" height="34" rx="9" fill="#143357"/><circle cx="17" cy="17" r="9" fill="none" stroke="#fff" stroke-width="1.4"/><path d="M12.5 17l3 3 6-6" fill="none" stroke="#fff" stroke-width="1.6"/></g>
    <g transform="translate(116 0)"><rect width="34" height="34" rx="9" fill="#143357"/><path d="M9 24h6l6-3M12 14v6M17 11v9M22 15v5" fill="none" stroke="#fff" stroke-width="1.6" stroke-linecap="round"/></g>
    <g transform="translate(233 0)"><rect width="34" height="34" rx="9" fill="#143357"/><circle cx="16" cy="17" r="9" fill="none" stroke="#fff" stroke-width="1.4"/><path d="M16 12v5h4" fill="none" stroke="#fff" stroke-width="1.6"/><circle cx="23" cy="23" r="3.5" fill="#fff"/></g>
    <g transform="translate(349 0)"><rect width="34" height="34" rx="9" fill="#143357"/><path d="M17 27v-9l-6-6M17 18l6-6M17 7v20M8 12h5v-5M26 12h-5v-5" fill="none" stroke="#fff" stroke-width="1.6" stroke-linecap="round"/></g>
  </svg>
  <div class="abs txt" style="left:75px;top:132px;width:60px;font-weight:800;line-height:1.3">Lorem ipsum dolor sit amet.</div>
  <div class="abs txt" style="left:191px;top:132px;width:60px;font-weight:800;line-height:1.3">Lorem ipsum dolor sit amet.</div>
  <div class="abs txt" style="left:308px;top:132px;width:60px;font-weight:800;line-height:1.3">Lorem ipsum dolor sit amet.</div>
  <div class="abs txt" style="left:424px;top:132px;width:60px;font-weight:800;line-height:1.3">Lorem ipsum dolor sit amet.</div>
  <p class="abs txt" style="left:52px;top:160px;width:82px;line-height:1.55">Lorem ipsum dolor sit amet, consectetuer adipiscing elit, sed diam nonummy nibh euismod tincidunt ut laoreet dolore magna aliquam erat volutpat.</p>
  <p class="abs txt" style="left:168px;top:160px;width:82px;line-height:1.55">Lorem ipsum dolor sit amet, consectetuer adipiscing elit, sed diam nonummy nibh euismod tincidunt ut laoreet dolore magna aliquam erat volutpat.</p>
  <p class="abs txt" style="left:285px;top:160px;width:82px;line-height:1.55">Lorem ipsum dolor sit amet, consectetuer adipiscing elit, sed diam nonummy nibh euismod tincidunt ut laoreet dolore magna aliquam erat volutpat.</p>
  <p class="abs txt" style="left:401px;top:160px;width:82px;line-height:1.55">Lorem ipsum dolor sit amet, consectetuer adipiscing elit, sed diam nonummy nibh euismod tincidunt ut laoreet dolore magna aliquam erat volutpat.</p>
  <div class="foot">Your presentation Title Goes Here | www.kluvotren.de</div>
  <div class="pg">03</div>
</section>

<!-- Image With Text -->
<section class="slide" style="left:616px;top:727px">
  <h2 class="s-title">Image With Text</h2>
  <div class="brand-mini"><i></i>KLUVOTREN</div>
  <div class="abs txt" style="left:40px;top:77px;width:215px">
    <p class="lead">Lorem ipsum dolor sit amet, consectetuer adipiscing elit, sed diam nonummy nibh euismod tincidunt.</p>
    <p style="margin-top:11px">Lorem ipsum dolor sit amet, consectetuer adipiscing elit, sed diam nonummy nibh euismod tincidunt ut laoreet dolore magna aliquam erat volutpat. Ut wisi enim ad minim veniam, quis nostrud exerci tation ullamcorper suscipit lobortis nisl ut aliquip ex ea commodo consequat.</p>
  </div>
  <div class="abs" style="left:40px;top:193px;width:3px;height:30px;background:var(--yellow)"></div>
  <p class="abs txt" style="left:55px;top:190px;width:200px;font-style:italic">Lorem ipsum dolor sit amet, consectetuer adipiscing elit, sed diam nonummy nibh euismod tincidunt ut laoreet dolore magna aliquam erat volutpat.</p>
  <div class="photo ph-green" style="left:274px;top:72px;width:228px;height:177px" role="img" aria-label="Tierärztin untersucht ein Pferd"></div>
  <div class="foot">Your presentation Title Goes Here | www.kluvotren.de</div>
  <div class="pg">04</div>
</section>

<!-- Single Paragraph -->
<section class="slide" style="left:79px;top:1038px">
  <h2 class="s-title">Single Paragraph</h2>
  <div class="brand-mini"><i></i>KLUVOTREN</div>
  <div class="abs txt" style="left:40px;top:98px;width:222px">
    <p class="lead">Lorem ipsum dolor sit amet, consectetuer adipiscing elit, sed diam nonummy nibh euismod tincidunt.</p>
    <p style="margin-top:11px">Lorem ipsum dolor sit amet, consectetuer adipiscing elit, sed diam nonummy nibh euismod tincidunt ut laoreet dolore magna aliquam erat volutpat. Ut wisi enim ad minim veniam, quis nostrud exerci tation ullamcorper suscipit lobortis nisl ut aliquip ex ea commodo consequat. Duis autem vel eum iriure dolor in hendrerit in vulputate velit esse molestie consequat, vel illum dolore eu feugiat nulla</p>
  </div>
  <div class="abs" style="left:295px;top:72px;width:180px;height:167px;background:var(--blue);border-radius:10px">
    <div style="position:absolute;left:78px;top:10px;font-size:30px;font-weight:800;color:var(--yellow);line-height:1">“</div>
    <p class="txt" style="position:absolute;left:15px;top:42px;width:150px;color:#fff;font-style:italic">Lorem ipsum dolor sit amet, consectetuer adipiscing elit, sed diam nonummy nibh euismod tincidunt ut laoreet dolore magna aliquam erat volutpat. Ut wisi enim ad minim veniam, quis nostrud exerci tation ullamcorper suscipit lobortis nisl ut aliquip ex ea commodo consequat, dolore eu feugiat nulla</p>
  </div>
  <div class="foot">Your presentation Title Goes Here | www.kluvotren.de</div>
  <div class="pg">05</div>
</section>

<!-- Project Overview -->
<section class="slide" style="left:616px;top:1038px">
  <h2 class="s-title">Project Overview</h2>
  <div class="brand-mini"><i></i>KLUVOTREN</div>
  <div class="abs" style="left:186px;top:77px;width:73px;height:74px;background:var(--blue);border-radius:22px 0 0 0;color:#fff;font-size:9px;font-weight:800;text-align:center;padding-top:27px;line-height:1.3">Quartal<br>One</div>
  <div class="abs" style="left:267px;top:77px;width:74px;height:74px;background:var(--yellow);border-radius:0 22px 0 0;color:#fff;font-size:9px;font-weight:800;text-align:center;padding-top:27px;line-height:1.3">Quartal<br>Two</div>
  <div class="abs" style="left:180px;top:159px;width:74px;height:76px;background:var(--yellow);border-radius:0 0 0 22px;color:#fff;font-size:9px;font-weight:800;text-align:center;padding-top:27px;line-height:1.3">Quartal<br>Three</div>
  <div class="abs" style="left:263px;top:159px;width:74px;height:76px;background:var(--blue);border-radius:0 0 22px 0;color:#fff;font-size:9px;font-weight:800;text-align:center;padding-top:27px;line-height:1.3">Quartal<br>Four</div>
  <svg class="abs" style="left:0;top:0" width="520" height="293" viewBox="0 0 520 293">
    <g fill="none" stroke="#9d8030" stroke-width=".7">
      <path d="M128 97 L170 98 L186 113"/><path d="M390 97 L360 98 L341 113"/>
      <path d="M128 185 L165 186 L180 197"/><path d="M390 185 L355 186 L337 197"/>
    </g>
    <g fill="#f7cd4e"><circle cx="186" cy="113" r="2"/><circle cx="180" cy="197" r="2"/></g>
    <g fill="#143357"><circle cx="341" cy="113" r="2"/><circle cx="337" cy="197" r="2"/></g>
  </svg>
  <div class="abs txt" style="left:42px;top:84px;line-height:1.5"><b>Quartal 1 Projects</b><ul class="dots" style="margin-top:4px"><li>Project 1 Name goes here</li><li>Project 2 Name goes here</li><li>Project 3 Name goes here</li><li>Project 4 Name goes here</li></ul></div>
  <div class="abs txt" style="left:388px;top:84px;line-height:1.5"><b>Quartal 2 Projects</b><ul class="dots" style="margin-top:4px"><li>Project 1 Name goes here</li><li>Project 2 Name goes here</li><li>Project 3 Name goes here</li><li>Project 4 Name goes here</li></ul></div>
  <div class="abs txt" style="left:42px;top:173px;line-height:1.5"><b>Quartal 3 Projects</b><ul class="dots" style="margin-top:4px"><li>Project 1 Name goes here</li><li>Project 2 Name goes here</li><li>Project 3 Name goes here</li><li>Project 4 Name goes here</li></ul></div>
  <div class="abs txt" style="left:388px;top:173px;line-height:1.5"><b>Quartal 3 Projects</b><ul class="dots" style="margin-top:4px"><li>Project 1 Name goes here</li><li>Project 2 Name goes here</li><li>Project 3 Name goes here</li><li>Project 4 Name goes here</li></ul></div>
  <div class="foot">Your presentation Title Goes Here | www.kluvotren.de</div>
  <div class="pg">06</div>
</section>

<!-- Our Service 11 -->
<section class="slide" style="left:79px;top:1349px">
  <h2 class="s-title">Our Service</h2>
  <div class="brand-mini"><i></i>KLUVOTREN</div>
  <svg class="abs" style="left:0;top:0" width="520" height="293" viewBox="0 0 520 293">
    <defs><filter id="sh" x="-10%" y="-10%" width="120%" height="130%"><feDropShadow dx="0" dy="1.5" stdDeviation="2.5" flood-color="#143357" flood-opacity=".14"/></filter></defs>
    <g filter="url(#sh)" fill="#fff">
      <rect x="48" y="75" width="204" height="75" rx="8"/><rect x="269" y="75" width="204" height="75" rx="8"/>
      <rect x="48" y="169" width="204" height="75" rx="8"/><rect x="269" y="169" width="204" height="75" rx="8"/>
    </g>
    <g fill="#f7cd4e">
      <rect x="53" y="80" width="62" height="65" rx="7"/><rect x="274" y="80" width="62" height="65" rx="7"/>
      <rect x="53" y="174" width="62" height="65" rx="7"/><rect x="274" y="174" width="62" height="65" rx="7"/>
    </g>
    <g class="icon-svg">
      <circle cx="84" cy="112" r="14"/><circle cx="84" cy="112" r="9"/><path d="M79 112l3.5 3.5 6.5-6.5"/>
      <circle cx="304" cy="112" r="13"/><path d="M304 104v8h6"/><circle cx="312" cy="120" r="4.5" fill="#f7cd4e"/><path d="M310 120h4M312 118v4"/>
      <path d="M70 220h10l10-5h6M74 205v8M80 200v13M86 206v7M92 198v15"/><circle cx="74" cy="198" r="3"/>
      <path d="M305 222v-10l-8-8M305 212l8-8M305 195v27M295 204h5v-5M315 204h-5v-5"/>
    </g>
  </svg>
  <div class="abs txt" style="left:123px;top:89px;width:120px"><b>Lorem ipsum dolor sit amet.</b><br>Lorem ipsum dolor sit amet, consectetuer adipiscing elit, sed diam nonummy nibh euismod.</div>
  <div class="abs txt" style="left:344px;top:89px;width:120px"><b>Lorem ipsum dolor sit amet.</b><br>Lorem ipsum dolor sit amet, consectetuer adipiscing elit, sed diam nonummy nibh euismod.</div>
  <div class="abs txt" style="left:123px;top:183px;width:120px"><b>Lorem ipsum dolor sit amet.</b><br>Lorem ipsum dolor sit amet, consectetuer adipiscing elit, sed diam nonummy nibh euismod.</div>
  <div class="abs txt" style="left:344px;top:183px;width:120px"><b>Lorem ipsum dolor sit amet.</b><br>Lorem ipsum dolor sit amet, consectetuer adipiscing elit, sed diam nonummy nibh euismod.</div>
  <div class="foot">Your presentation Title Goes Here | www.kluvotren.de</div>
  <div class="pg">11</div>
</section>

<!-- Our Team 07 -->
<section class="slide" style="left:616px;top:1349px">
  <h2 class="s-title" style="left:33px;top:32px">Our<br>Team</h2>
  <div class="brand-mini"><i></i>KLUVOTREN</div>
  <div class="photo ph-light" style="left:101px;top:71px;width:125px;height:174px;border-radius:6px;background:linear-gradient(180deg,#eef0f2 0%,#c7ced6 55%,#1d3b62 100%)" role="img" aria-label="Porträt des Geschäftsführers"></div>
  <div class="abs" style="left:101px;top:216px;width:125px;text-align:center;color:#fff;font-size:6.8px;font-weight:600;line-height:1.3"><span style="color:var(--yellow);font-size:9px;font-weight:800">Dr. Tobias Brenner</span><br>Geschäftsführer</div>
  <div class="abs txt" style="left:252px;top:80px;width:240px">
    <p class="lead" style="font-style:italic">Lorem ipsum dolor sit amet, consectetuer adipiscing elit, sed diam nonummy nibh euismod tincidunt.</p>
    <p style="margin-top:8px">Lorem ipsum dolor sit amet, consectetuer adipiscing elit, sed diam nonummy nibh euismod tincidunt ut laoreet dolore magna aliquam erat volutpat.</p>
    <div style="display:flex;gap:10px;margin-top:7px"><span style="color:var(--gold)">01</span><span>Lorem ipsum dolor sit amet, consectetuer adipiscing elit, sed diam nonummy nibh euismod.</span></div>
    <div style="display:flex;gap:10px;margin-top:7px"><span style="color:var(--gold)">02</span><span>Lorem ipsum dolor sit amet, consectetuer adipiscing elit, sed diam nonummy nibh euismod.</span></div>
    <div style="display:flex;gap:10px;margin-top:7px"><span style="color:var(--gold)">03</span><span>Lorem ipsum dolor sit amet, consectetuer adipiscing elit, sed diam nonummy nibh euismod.</span></div>
  </div>
  <div class="foot">Your presentation Title Goes Here | www.kluvotren.de</div>
  <div class="pg">07</div>
</section>

<!-- Our Service 12 -->
<section class="slide" style="left:79px;top:1660px">
  <h2 class="s-title">Our Service</h2>
  <div class="brand-mini"><i></i>KLUVOTREN</div>
  <div class="abs" style="left:0;top:189px;width:258px;height:104px;background:var(--blue)"></div>
  <div class="photo ph-light" style="left:40px;top:70px;width:201px;height:180px;border-radius:12px" role="img" aria-label="Computertomograph im Behandlungsraum"></div>
  <svg class="abs" style="left:0;top:0" width="520" height="293" viewBox="0 0 520 293">
    <g filter="url(#sh)">
      <rect x="277" y="76" width="193" height="30" rx="6" fill="#fff"/>
      <rect x="277" y="121" width="193" height="30" rx="6" fill="#f7cd4e"/>
      <rect x="277" y="165" width="193" height="30" rx="6" fill="#fff"/>
      <rect x="277" y="209" width="193" height="30" rx="6" fill="#f7cd4e"/>
    </g>
    <g>
      <circle cx="453" cy="91" r="11" fill="#f7cd4e"/><circle cx="453" cy="136" r="11" fill="#fff"/>
      <circle cx="453" cy="180" r="11" fill="#f7cd4e"/><circle cx="453" cy="224" r="11" fill="#fff"/>
    </g>
    <g class="icon-svg" stroke-width="1.2">
      <circle cx="453" cy="91" r="6.5"/><path d="M450 91l2 2 4-4"/>
      <circle cx="453" cy="136" r="6"/><path d="M453 132.5v3.5h3"/>
      <path d="M447 185h5l4-2M449 180v3M453 177v6M457 179v4"/>
      <path d="M453 230v-5l-4-4M453 225l4-4M453 218v12"/>
    </g>
  </svg>
  <div class="abs txt" style="left:290px;top:80px;font-size:6.5px;line-height:1.55;font-weight:600">Lorem ipsum dolor sit amet,<br><b>consectetuer adipiscing elit, sed diam.</b></div>
  <div class="abs txt" style="left:290px;top:125px;font-size:6.5px;line-height:1.55;font-weight:600">Lorem ipsum dolor sit amet,<br><b>consectetuer adipiscing elit, sed diam.</b></div>
  <div class="abs txt" style="left:290px;top:169px;font-size:6.5px;line-height:1.55;font-weight:600">Lorem ipsum dolor sit amet,<br><b>consectetuer adipiscing elit, sed diam.</b></div>
  <div class="abs txt" style="left:290px;top:213px;font-size:6.5px;line-height:1.55;font-weight:600">Lorem ipsum dolor sit amet,<br><b>consectetuer adipiscing elit, sed diam.</b></div>
  <div class="foot" style="color:#fff">Your presentation Title Goes Here | www.kluvotren.de</div>
  <div class="pg">12</div>
</section>

<!-- Our Team 08 -->
<section class="slide" style="left:616px;top:1660px">
  <h2 class="s-title">Our Team</h2>
  <div class="brand-mini"><i></i>KLUVOTREN</div>
  <div class="abs" style="left:0;top:225px;width:520px;height:68px;background:var(--blue)"></div>
  <div class="abs" style="left:40px;top:88px;width:107px;height:167px;background:#fff;border-radius:10px;box-shadow:0 2px 6px rgba(20,51,87,.12)"></div>
  <div class="abs" style="left:159px;top:88px;width:107px;height:167px;background:#fff;border-radius:10px;box-shadow:0 2px 6px rgba(20,51,87,.12)"></div>
  <div class="abs" style="left:277px;top:88px;width:107px;height:167px;background:#fff;border-radius:10px;box-shadow:0 2px 6px rgba(20,51,87,.12)"></div>
  <div class="abs" style="left:395px;top:88px;width:107px;height:167px;background:#fff;border-radius:10px;box-shadow:0 2px 6px rgba(20,51,87,.12)"></div>
  <div class="photo ph-light" style="left:40px;top:88px;width:107px;height:70px;border-radius:10px 10px 0 0" role="img" aria-label="Porträt Teammitglied"></div>
  <div class="photo ph-light" style="left:159px;top:88px;width:107px;height:70px;border-radius:10px 10px 0 0" role="img" aria-label="Porträt Teammitglied"></div>
  <div class="photo ph-light" style="left:277px;top:88px;width:107px;height:70px;border-radius:10px 10px 0 0" role="img" aria-label="Porträt Teammitglied"></div>
  <div class="photo ph-light" style="left:395px;top:88px;width:107px;height:70px;border-radius:10px 10px 0 0" role="img" aria-label="Porträt Teammitglied"></div>
  <div class="abs txt" style="left:40px;top:160px;width:107px;text-align:center;line-height:1.25"><b>Dr. Tobias Brenner</b><br><span style="font-size:5.5px">Geschäftsführer</span></div>
  <div class="abs txt" style="left:159px;top:160px;width:107px;text-align:center;line-height:1.25"><b>Helga Wintrop</b><br><span style="font-size:5.5px">Geschäftsführer</span></div>
  <div class="abs txt" style="left:277px;top:160px;width:107px;text-align:center;line-height:1.25"><b>Jonas Feldt</b><br><span style="font-size:5.5px">Geschäftsführer</span></div>
  <div class="abs txt" style="left:395px;top:160px;width:107px;text-align:center;line-height:1.25"><b>Klara Lindqvist</b><br><span style="font-size:5.5px">Geschäftsführer</span></div>
  <ul class="abs txt dots" style="left:60px;top:187px;line-height:1.6"><li>Project 1 Name</li><li>Project 1 Name</li><li>Project 1 Name</li><li>Project 1 Name</li></ul>
  <ul class="abs txt dots" style="left:179px;top:187px;line-height:1.6"><li>Project 1 Name</li><li>Project 1 Name</li><li>Project 1 Name</li><li>Project 1 Name</li></ul>
  <ul class="abs txt dots" style="left:297px;top:187px;line-height:1.6"><li>Project 1 Name</li><li>Project 1 Name</li><li>Project 1 Name</li><li>Project 1 Name</li></ul>
  <ul class="abs txt dots" style="left:415px;top:187px;line-height:1.6"><li>Project 1 Name</li><li>Project 1 Name</li><li>Project 1 Name</li><li>Project 1 Name</li></ul>
  <div class="foot" style="color:#fff">Your presentation Title Goes Here | www.kluvotren.de</div>
  <div class="pg">08</div>
</section>

<!-- Three Column 09 -->
<section class="slide" style="left:79px;top:1971px">
  <h2 class="s-title">Three Column</h2>
  <div class="brand-mini"><i></i>KLUVOTREN</div>
  <p class="abs txt" style="left:40px;top:69px;width:410px">Lorem ipsum dolor sit amet, consectetuer adipiscing elit, sed diam nonummy nibh euismod tincidunt ut laoreet dolore magna aliquam erat volutpat. Ut wisi enim ad minim veniam, quis nostrud exerci tation ullamcorper suscipit lobortis nisl ut aliquip ex ea commodo consequat.</p>
  <div class="abs txt" style="left:39px;top:120px;width:145px"><div class="num-lite">01</div><p class="lead" style="margin-top:3px">Lorem ipsum dolor sit amet, consectetuer adipiscing elit, sed diam.</p><p style="margin-top:5px">Lorem ipsum dolor sit amet, consectetuer adipiscing elit, sed diam nonummy nibh euismod tincidunt ut laoreet dolore magna aliquam erat volutpat. Ut wisi enim ad minim veniam, quis nostrud exerci tation ullamcorper suscipit lobortis nisl ut aliquip ex ea.</p></div>
  <div class="abs txt" style="left:199px;top:120px;width:145px"><div class="num-lite">02</div><p class="lead" style="margin-top:3px">Lorem ipsum dolor sit amet, consectetuer adipiscing elit, sed diam.</p><p style="margin-top:5px">Lorem ipsum dolor sit amet, consectetuer adipiscing elit, sed diam nonummy nibh euismod tincidunt ut laoreet dolore magna aliquam erat volutpat. Ut wisi enim ad minim veniam, quis nostrud exerci tation ullamcorper suscipit lobortis nisl ut aliquip ex ea.</p></div>
  <div class="abs txt" style="left:358px;top:120px;width:145px"><div class="num-lite">03</div><p class="lead" style="margin-top:3px">Lorem ipsum dolor sit amet, consectetuer adipiscing elit, sed diam.</p><p style="margin-top:5px">Lorem ipsum dolor sit amet, consectetuer adipiscing elit, sed diam nonummy nibh euismod tincidunt ut laoreet dolore magna aliquam erat volutpat. Ut wisi enim ad minim veniam, quis nostrud exerci tation ullamcorper suscipit lobortis nisl ut aliquip ex ea.</p></div>
  <div class="foot">Your presentation Title Goes Here | www.kluvotren.de</div>
  <div class="pg">09</div>
</section>

<!-- Three Column 10 -->
<section class="slide" style="left:616px;top:1971px">
  <h2 class="s-title">Three Column</h2>
  <div class="brand-mini"><i></i>KLUVOTREN</div>
  <div class="abs" style="left:169px;top:100px;width:1px;height:160px;background:var(--rule)"></div>
  <div class="abs" style="left:328px;top:100px;width:1px;height:160px;background:var(--rule)"></div>
  <div class="abs txt" style="left:40px;top:98px;width:118px"><div class="num-lite">01</div><p class="lead" style="margin-top:2px">Lorem ipsum dolor sit amet, consectetuer adipiscing.</p><p style="margin-top:6px">Lorem ipsum dolor sit amet, consectetuer adipiscing elit, sed diam nonummy nibh euismod tincidunt ut laoreet dolore magna aliquam erat volutpat. Ut wisi enim ad minim veniam, quis nostrud exerci tation ullamcorper suscipit lobortis nisl ut aliquip ex ea.</p></div>
  <div class="abs txt" style="left:198px;top:98px;width:118px"><div class="num-lite">02</div><p class="lead" style="margin-top:2px">Lorem ipsum dolor sit amet, consectetuer adipiscing.</p><p style="margin-top:6px">Lorem ipsum dolor sit amet, consectetuer adipiscing elit, sed diam nonummy nibh euismod tincidunt ut laoreet dolore magna aliquam erat volutpat. Ut wisi enim ad minim veniam, quis nostrud exerci tation ullamcorper suscipit lobortis nisl ut aliquip ex ea.</p></div>
  <div class="abs txt" style="left:356px;top:98px;width:118px"><div class="num-lite">03</div><p class="lead" style="margin-top:2px">Lorem ipsum dolor sit amet, consectetuer adipiscing.</p><p style="margin-top:6px">Lorem ipsum dolor sit amet, consectetuer adipiscing elit, sed diam nonummy nibh euismod tincidunt ut laoreet dolore magna aliquam erat volutpat. Ut wisi enim ad minim veniam, quis nostrud exerci tation ullamcorper suscipit lobortis nisl ut aliquip ex ea.</p></div>
  <div class="foot">Your presentation Title Goes Here | www.kluvotren.de</div>
  <div class="pg">10</div>
</section>

<!-- Schlussfolie -->
<section class="slide dark" style="left:616px;top:2282px">
  <div class="photo ph-blue" style="left:11px;top:-10px;width:109px;height:86px;opacity:.7" role="img" aria-label="Behandlung in der Praxis"></div>
  <div class="photo ph-green" style="left:11px;top:92px;width:109px;height:140px" role="img" aria-label="Tierärztin mit Pferd"></div>
  <div class="photo ph-blue" style="left:11px;top:241px;width:109px;height:62px;opacity:.7" role="img" aria-label="Praxisteam"></div>
  <div class="photo ph-blue" style="left:128px;top:-10px;width:108px;height:67px;opacity:.6" role="img" aria-label="Praxisräume"></div>
  <div class="photo ph-light" style="left:128px;top:61px;width:108px;height:140px" role="img" aria-label="Team bespricht sich am Laptop"></div>
  <div class="photo ph-warm" style="left:128px;top:209px;width:108px;height:94px;opacity:.85" role="img" aria-label="Golden Retriever Welpe"></div>
  <div class="abs" style="left:299px;top:38px;display:flex;align-items:center;gap:8px;font-size:20px;font-weight:600;color:var(--yellow)"><span style="width:22px;height:22px;border-radius:50%;background:var(--yellow);display:block"></span>KLUVOTREN</div>
  <h1 class="abs" style="left:296px;top:116px;font-size:24px;font-weight:800;line-height:1.25">Thank You for<br><span style="color:var(--yellow)">Your Attention</span></h1>
  <div class="btn" style="left:296px;top:187px;width:182px"><svg viewBox="0 0 10 10"><path d="M1 0 L10 5 L1 10Z" fill="#143357"/></svg>Lorem ipsum dolor sit amet</div>
  <div class="abs" style="left:20px;bottom:14px;font-size:5.5px">info@kluvotren.de | www.kluvotren.de</div>
  <div class="abs" style="right:45px;bottom:14px;font-size:5.5px">07 Februar 2025 | Created by Lena Hausmann</div>
</section>

</body>
</html>
```